Stylish Business Cards Wanted

- DOUBLE SIDED Design Required -

High end, edgy cards for a corporate and personal stylist. Must include logo,
Name: Belinda Harwick
Title: Director and Stylist
telephone : +61 8 7142 5809
email: belinda@theloombriefing.example
website: theloombriefing.example
Tag: Corporate Workwear & Uniform Specialist | Personal Stylist
Would like nice icons for telephone, email, website

Target Market(s)

Businesses wanting stylish uniforms, people wanting stylish wardrobes

Industry/Entity Type

Corporate Workwear Stylist

Contact Information for Business Card

I would like black, white and gold foiling incorporated in the design - possibly a touch of the other colours on my branding guide attached Name: Belinda Harwick Title: Director and Stylist telephone : +61 8 7142 5809 email: belinda@theloombriefing.example website: theloombriefing.example Tag: Corporate Workwear & Uniform Specialist | Personal Stylist Would like nice icons for telephone, email, website

Font styles to use
Other font styles liked:
• Raleway

Colors

Designer to choose colors to be used in the design.

Requirements
Must have
• Gold foil accents

```html
<!DOCTYPE html>
<html lang="en">
<head>
<meta charset="utf-8">
<title>The Loom Briefing – Business Cards</title>
<link rel="stylesheet" href="https://fonts.googleapis.com/css2?family=Open+Sans:wght@400&family=Raleway:wght@600&display=swap">
<style>
  :root {
    --backdrop: #ecebe8;
    --card: #ffffff;
    --ink: #000000;
    --charcoal: #333333;
    --gold: #e3c060;
    --paper-text: #ffffff;
  }
  html, body {
    margin: 0;
    width: 1200px;
    height: 960px;
    overflow: hidden;
    background: var(--backdrop);
  }
  .canvas {
    position: relative;
    width: 1200px;
    height: 960px;
  }
  .card {
    position: absolute;
    left: 314px;
    width: 600px;
    height: 343px;
    background: var(--card);
    overflow: hidden;
    box-shadow: 0 2px 6px rgba(0,0,0,0.18);
  }
  .card--front { top: 129px; }
  .card--back { top: 488px; }

  .contact-panel {
    position: absolute;
    left: 0;
    top: 42px;
    width: 283px;
    height: 260px;
    background: var(--ink);
    color: var(--paper-text);
    font-family: "Open Sans", sans-serif;
  }
  .contact-panel__name {
    position: absolute;
    left: 28px;
    top: 53px;
    margin: 0;
    font-family: Arial, "Open Sans", sans-serif;
    font-weight: 400;
    font-size: 20px;
    line-height: 1;
    letter-spacing: 0.2px;
  }
  .contact-panel__title {
    position: absolute;
    left: 29px;
    top: 75px;
    margin: 0;
    font-size: 9.5px;
  }
  .contact-list {
    position: absolute;
    left: 28px;
    top: 119px;
    margin: 0;
    padding: 0;
    list-style: none;
    font-size: 12.5px;
  }
  .contact-list__item {
    display: flex;
    align-items: center;
    height: 14px;
    margin-bottom: 14px;
    white-space: nowrap;
  }
  .contact-list__icon {
    width: 15px;
    height: 14px;
    margin-right: 9px;
    flex: none;
  }

  .gold-tab {
    position: absolute;
    right: 0;
    top: 49px;
    width: 19px;
    height: 240px;
    background: var(--gold);
    border-radius: 19px 0 0 19px;
  }

  .brand {
    position: absolute;
    display: flex;
    align-items: center;
    gap: 8px;
    font-family: "Raleway", sans-serif;
    font-weight: 600;
    font-size: 24px;
    color: var(--charcoal);
    white-space: nowrap;
    transform: translate(-50%, -50%);
  }
  .brand__mark {
    width: 10px;
    height: 10px;
    background: var(--gold);
  }
  .card--front .brand { left: 429px; top: 171px; }
  .card--back .brand { left: 300px; top: 160px; }

  .tagline {
    position: absolute;
    left: 0;
    right: 0;
    top: 188px;
    margin: 0;
    text-align: center;
    font-family: "Open Sans", sans-serif;
    font-size: 11px;
    letter-spacing: 0.5px;
    color: var(--charcoal);
  }

  .website {
    position: absolute;
    left: 0;
    right: 0;
    top: 296px;
    margin: 0;
    text-align: center;
    font-family: "Open Sans", sans-serif;
    font-size: 16px;
    letter-spacing: 4px;
    color: var(--charcoal);
  }
</style>
</head>
<body>
<main class="canvas">

  <section class="card card--front" aria-label="Card front">
    <div class="contact-panel">
      <h1 class="contact-panel__name">BELINDA HARWICK</h1>
      <p class="contact-panel__title">Director and Stylist</p>
      <ul class="contact-list">
        <li class="contact-list__item">
          <svg class="contact-list__icon" viewBox="0 0 16 16" aria-hidden="true">
            <path d="M3.5 1.5 L5.8 1.2 L7 4.6 L5.4 5.8 C6.2 7.8 8.2 9.8 10.2 10.6 L11.4 9 L14.8 10.2 L14.5 12.5 C14.3 13.8 13 14.6 11.6 14.3 C6.6 13.2 2.8 9.4 1.7 4.4 C1.4 3 2.2 1.7 3.5 1.5 Z" fill="none" stroke="#fff" stroke-width="1.4" stroke-linejoin="round"/>
            <path d="M10 1.5 A4.5 4.5 0 0 1 14.5 6 M10 3.8 A2.2 2.2 0 0 1 12.2 6" fill="none" stroke="#fff" stroke-width="1.2" stroke-linecap="round"/>
          </svg>
          <span>+61 8 7142 5809</span>
        </li>
        <li class="contact-list__item">
          <svg class="contact-list__icon" viewBox="0 0 16 16" aria-hidden="true">
            <circle cx="8" cy="8" r="6.5" fill="none" stroke="#fff" stroke-width="1.2"/>
            <ellipse cx="8" cy="8" rx="2.8" ry="6.5" fill="none" stroke="#fff" stroke-width="1"/>
            <path d="M1.5 8 H14.5 M2.6 4.6 H13.4 M2.6 11.4 H13.4" stroke="#fff" stroke-width="0.9"/>
          </svg>
          <span>www.theloombriefing.example</span>
        </li>
        <li class="contact-list__item">
          <svg class="contact-list__icon" viewBox="0 0 16 16" aria-hidden="true">
            <rect x="1" y="3" width="14" height="10" fill="#fff"/>
            <path d="M1 3 L8 9 L15 3 M1 13 L6 7.8 M15 13 L10 7.8" fill="none" stroke="#000" stroke-width="0.9"/>
          </svg>
          <span>belinda@theloombriefing.example</span>
        </li>
      </ul>
    </div>
    <div class="brand"><span class="brand__mark"></span><span>The Loom Briefing</span></div>
    <div class="gold-tab"></div>
  </section>

  <section class="card card--back" aria-label="Card back">
    <div class="brand"><span class="brand__mark"></span><span>The Loom Briefing</span></div>
    <p class="tagline">Corporate Workwear &amp; Uniform Specialist | Personal Stylist</p>
    <p class="website">www.theloombriefing.example</p>
  </section>

</main>
</body>
</html>
```